Teeth Whitening Clinic Website Redesign - Social Proof Theme

NEW TEETH SITEREVAMP CURRENT WEBSITE:WWW.SANDIEGOSTEETHWHITENING.COMTHEME:SOCIAL PROOF/5 STAR REVIEWS/TESTIMONIALS THEME:https://maps.example.net/QxRvPLoKzN84 I want a testimonial themed, social proof themed website so customers will be sold by testimonials all over the website….I like a nice clean simple site but with all important factors standing out like CALLS TO ACTIONS, for example the $99 special link in header on original design. Also, testimonials throughout the website placed methodically as not to be FORCED and CLUTTEREDKeep all same exact content for all pages and elements of current design. All buttons, calls to action, navigation, etc. Please do not leave anything out from current design. SPECIAL INSTRUCTIONS for banner image:I want to use actual customer photos inside the banner image in a way that really pops and grabs attention. Please grab some customer photos from my PG Account, fk or rateway account: Also, I want to integrate 5 star rateway logo, friendbook review 5 stars icon, searchly business page 5 stars icon, etc. on the banner as well to show social proof as much as possible. Actual customer photos to be used throughout website:https://www.photogram.example/brightharborsmilestudioplace/ https://www.friendbook.com/SDTeethWhitening/https://www.reviewhub.example/biz/bright-harbor-smile-studio-place-bright-harbor-5 Reviews:https://www.reviewhub.example/biz/bright-harbor-smile-studio-place-bright-harbor-5 https://www.friendbook.com/pg/SDTeethWhitening/reviews/?ref=page_internalhttps://goo.gl/maps/TmJcABLAJwC2 Please do home page first to come up with theme then after approval home page we can move forward additional pages.

Target Market(s)

PEOPLE THAT CARE ABOUT DENTAL HYGEINE AND OR CARE ABOUT THEIR TEETH SMILE

Industry/Entity Type

Dental Clinic

Number of Pages Required

5+ page

Colors

Designer to choose colors to be used in the design.

Requirements
Must have
• NEW TEETH SITE
• REVAMP CURRENT WEBSITE:
• WWW.BRIGHTHARBORSMILESTUDIO.EXAMPLE
• THEME:
• SOCIAL PROOF/5 STAR REVIEWS/TESTIMONIALS THEME:
• https://maps.example.net/QxRvPLoKzN84
• I want a testimonial themed, social proof themed website so customers will be sold by testimonials all over the website….I like a nice clean simple site but with all important factors standing out like CALLS TO ACTIONS, for example the $99 special link in header on original design. Also, testimonials throughout the website placed methodically as not to be FORCED and CLUTTERED
• Keep all same exact content for all pages and elements of current design. All buttons, calls to action, navigation, etc. Please do not leave anything out from current design.
• SPECIAL INSTRUCTIONS for banner image:
• I want to use actual customer photos inside the banner image in a way that really pops and grabs attention. Please grab some customer photos from my PG Account, fk or rateway account:
• Also, I want to integrate 5 star rateway logo, friendbook review 5 stars icon, searchly business page 5 stars icon, etc. on the banner as well to show social proof as much as possible.
• Actual customer photos to be used throughout website:
• https://www.photogram.example/brightharborsmilestudioplace/
• https://www.friendbook.example/BHSmileStudio/
• https://www.reviewhub.example/biz/bright-harbor-smile-studio-place-bright-harbor-5
• Reviews:
• https://www.friendbook.example/pg/BHSmileStudio/reviews/?ref=page_internal
• Please do home page first to come up with theme then after approval home page we can move forward additional pages.
Nice to have
• NEW TEETH SITE
• REVAMP CURRENT WEBSITE:
• THEME:
• Reviews:
Should not have
• NEW TEETH SITE
• REVAMP CURRENT WEBSITE:
• THEME:
• Reviews:

```html
<!DOCTYPE html>
<html lang="en">
<head>
<meta charset="utf-8">
<title>Bright Harbor Smile Studio</title>
<link href="https://fonts.googleapis.com/css2?family=Roboto:wght@400;500;700&family=Open+Sans:wght@400;600&display=swap" rel="stylesheet">
<style>
:root{
  --teal:#35b8d1;
  --teal-dark:#2aa3bb;
  --ink:#222;
  --text:#666;
  --muted:#888;
  --line:#e3e3e3;
  --grey-head:#6b6b6b;
  --foot-band:#6c6c6c;
  --foot:#5e5e5e;
  --foot-bottom:#555;
  --white:#fff;
}
*{box-sizing:border-box;margin:0;padding:0}
html,body{width:1200px;height:3196px;overflow:hidden}
body{font-family:"Open Sans",sans-serif;color:var(--text);background:var(--white);position:relative}
.abs{position:absolute}
h1,h2,h3,h4{font-family:"Roboto",sans-serif;font-weight:500}

/* top bar */
.topbar{position:absolute;left:0;top:0;width:1200px;height:35px;background:var(--teal);color:var(--white);font-size:12px}
.topbar .phone{left:112px;top:10px;display:flex;gap:6px;align-items:center}
.topbar .hours{left:308px;top:10px}
.topbar .social{right:112px;top:9px;display:flex;gap:14px;font-size:11px;font-weight:600}

/* header */
.header{position:absolute;left:0;top:35px;width:1200px;height:79px;border-bottom:1px solid var(--line)}
.brand{left:112px;top:8px;display:flex;align-items:center;gap:10px}
.brand-mark{width:58px;height:58px;border-radius:50%;border:2px solid #cfd6da;flex:none}
.brand-name{font-family:"Roboto",sans-serif;font-size:19px;line-height:20px;color:#555;font-weight:500}
.deal{left:414px;top:20px;display:flex;gap:14px;font-size:12px;color:var(--muted);line-height:19px}
.addr{left:670px;top:20px;display:flex;gap:14px;font-size:12px;color:var(--muted);line-height:19px}
.btn-outline{display:inline-block;border:1px solid var(--teal);color:var(--teal);border-radius:3px;font-size:12px;font-weight:600;text-align:center}
.header .btn-outline{position:absolute;left:905px;top:21px;width:183px;height:37px;line-height:35px}

/* nav */
.nav{position:absolute;left:0;top:114px;width:1200px;height:39px;display:flex;justify-content:space-between;padding:0 112px 0 116px;align-items:center;font-family:"Roboto",sans-serif;font-size:13px;font-weight:500;color:#222}

/* hero */
.hero{position:absolute;left:0;top:153px;width:1200px;height:495px}
.ph-left{left:0;top:0;width:376px;height:495px;background:linear-gradient(160deg,#b6a89a,#d9cfc4 50%,#8e7d7a)}
.ph-rt{left:816px;top:0;width:384px;height:240px;background:linear-gradient(160deg,#9e8e82,#d6cbc2 60%,#7b6f6d)}
.ph-rb{left:816px;top:240px;width:384px;height:255px;background:linear-gradient(200deg,#c9b9ad,#8a7466 60%,#5f4e47)}
.hero-mid{left:376px;top:0;width:440px;height:495px;background:linear-gradient(180deg,#3fbfd6,#35b3cc);color:var(--white);text-align:center}
.hero-mid h1{margin-top:88px;font-size:34px;line-height:38px;font-weight:500}
.hero-mid p{margin-top:14px;font-size:16px;line-height:26px}
.reviews{margin-top:34px;display:flex;justify-content:center;gap:22px;align-items:center}
.review{display:flex;align-items:center;gap:7px;font-family:"Open Sans",sans-serif;font-weight:600;font-size:16px;color:var(--white)}
.review i{width:14px;height:14px;border-radius:50%;background:var(--white);display:block}
.hero-social{margin-top:38px;display:flex;justify-content:center;gap:8px}
.hero-social span{width:39px;height:39px;border:1px solid var(--white);border-radius:50%;font-size:12px;font-weight:600;line-height:37px}

/* about */
.about-h{left:112px;top:736px;font-size:29px;line-height:36px;color:var(--ink);font-weight:400}
.about-h b{display:block;color:var(--teal);font-weight:500}
.about-sub{left:112px;top:820px;font-size:21px;color:#333;font-weight:300;font-family:"Roboto",sans-serif}
.about-p{left:112px;top:870px;width:432px;font-size:12.5px;line-height:26px;color:var(--text)}
.video{left:600px;top:740px;width:488px;height:274px;background:radial-gradient(circle at 50% 45%,#fff,#ececec 60%,#d6d6d6);border:1px solid var(--line)}
.video .play{position:absolute;left:208px;top:100px;width:72px;height:72px;border-radius:50%;background:rgba(53,184,209,.75)}
.video .vname{position:absolute;left:0;width:100%;top:180px;text-align:center;font-family:"Roboto",sans-serif;font-size:18px;color:#555}

/* why */
.sec-title{position:absolute;left:0;width:1200px;text-align:center;font-family:"Roboto",sans-serif;font-size:30px;font-weight:500;color:var(--ink)}
.sec-title em{font-style:normal;color:var(--teal)}
.why{left:112px;top:1183px;width:976px;display:flex;justify-content:space-between}
.feature{width:132px;text-align:center;font-family:"Roboto",sans-serif;font-size:21px;color:#333}
.feature .ring{width:131px;height:131px;border:1px solid var(--teal);border-radius:50%;display:flex;align-items:center;justify-content:center;margin-bottom:26px;position:relative}
.feature.active .ring{background:var(--teal)}
.feature.active .ring::before{content:"";position:absolute;inset:8px;border:1px solid rgba(255,255,255,.8);border-radius:50%}
.feature.active .ring::after{content:"";position:absolute;bottom:-10px;left:56px;border:10px solid transparent;border-top-color:var(--teal);border-bottom:0}

/* how */
.how{left:0;top:1443px;width:1200px;height:422px;background:linear-gradient(180deg,#3ab7cf,#37b0c9 60%,#34aac4);color:var(--white);text-align:center}
.how h2{margin-top:88px;font-size:30px;font-weight:500}
.how p{margin:22px auto 0;width:840px;font-size:13px;line-height:26.5px}
.how .btn{display:inline-block;margin-top:38px;width:147px;height:37px;line-height:35px;border:1px solid var(--white);border-radius:3px;font-size:13px;font-weight:600;font-family:"Roboto",sans-serif}

/* compare */
.compare{left:113px;top:2014px;width:975px;border-collapse:collapse;font-size:13px;text-align:center}
.compare th{height:63px;font-family:"Roboto",sans-serif;font-size:22px;font-weight:500;color:#333;border:1px solid var(--line)}
.compare td{height:42px;border:1px solid var(--line);color:var(--muted)}
.compare .feat{background:var(--grey-head);color:var(--white);width:177px;font-size:15px;border-color:#8a8a8a}
.compare th.feat{font-size:25px}
.compare .hl{background:var(--teal);color:var(--white);border-color:var(--teal)}

/* testimonial */
.quote{left:158px;top:2450px;width:860px;font-size:13px;line-height:28px;color:var(--text);padding-left:30px}
.quote .mark{position:absolute;left:0;top:0;font-family:"Roboto",sans-serif;font-size:18px;color:#444}
.avatar{left:158px;top:2556px;width:103px;height:103px;border-radius:50%;background:linear-gradient(160deg,#6b4a3c,#c9a08a 55%,#3a2a25)}
.t-meta{left:281px;top:2572px;font-size:13px;font-style:italic;line-height:29px;color:#333}
.t-meta .link{color:var(--teal);font-size:12px}
.more{position:absolute;left:848px;top:2587px;width:161px;height:41px;line-height:39px}

/* footer */
.f-band{left:0;top:2766px;width:1200px;height:104px;background:var(--foot-band);color:var(--white);font-size:12px;line-height:21px}
.f-item{position:absolute;top:30px;display:flex;gap:12px;align-items:center}
.f-ico{width:42px;height:42px;border-radius:50%;background:var(--teal);display:flex;align-items:center;justify-content:center;flex:none}
.footer{left:0;top:2870px;width:1200px;height:272px;background:var(--foot);color:var(--white)}
.fcol{position:absolute;top:50px}
.fcol h4{font-family:"Open Sans",sans-serif;font-weight:400;font-size:21px;margin-bottom:18px}
.fcol li{list-style:none;font-size:12px;line-height:21.5px}
.news{display:flex;width:290px;height:43px}
.news span{flex:1;background:var(--white);color:#555;font-size:13px;padding:12px 15px}
.news b{width:46px;background:var(--teal);display:flex;align-items:center;justify-content:center}
.bottom{left:0;top:3142px;width:1200px;height:54px;background:var(--foot-bottom);color:var(--white);font-size:12px}
.bottom .copy{position:absolute;left:112px;top:19px}
.bottom .connect{position:absolute;right:112px;top:19px;display:flex;gap:8px}
</style>
</head>
<body>

<div class="topbar">
  <div class="abs phone"><svg width="11" height="11" viewBox="0 0 24 24"><path fill="#fff" d="M6.6 10.8a15 15 0 006.6 6.6l2.2-2.2a1 1 0 011-.25 11.4 11.4 0 003.6.57 1 1 0 011 1V20a1 1 0 01-1 1A17 17 0 013 4a1 1 0 011-1h3.5a1 1 0 011 1c0 1.25.2 2.45.57 3.57a1 1 0 01-.25 1z"/></svg>1-555-014-2290</div>
  <div class="abs hours">Clinic Open: Mon-Fri 9:15 am to 5:30 pm Sat 10am to 2pm : Book Appointments: Mon-Fri 830 am to 5 pm</div>
  <div class="abs social"><span>fk</span><span>ch</span><span>PG</span></div>
</div>

<header class="header">
  <div class="abs brand"><span class="brand-mark"></span><span class="brand-name">Bright Harbor<br>Smile Studio</span></div>
  <div class="abs deal">
    <svg width="16" height="30" viewBox="0 0 16 30"><text x="1" y="24" font-family="Roboto" font-size="28" font-weight="700" fill="#35b8d1">$</text></svg>
    <span>Click Here to Get Our $99 Teeth<br>Whiting Deal (Reg: $378)</span>
  </div>
  <div class="abs addr">
    <svg width="16" height="24" viewBox="0 0 24 34"><path fill="#35b8d1" d="M12 0a12 12 0 00-12 12c0 9 12 22 12 22s12-13 12-22A12 12 0 0012 0zm0 17a5 5 0 110-10 5 5 0 010 10z"/></svg>
    <span>418 Harborview Way #205<br>Bayside, CA 90210</span>
  </div>
  <span class="btn-outline">Book Appointment Online</span>
</header>

<nav class="nav">
  <span>HOME</span><span>OUR PROCESS</span><span>PHOTOS</span><span>FREE TREATMENTS</span><span>TESTIMONIALS</span><span>BLOG</span><span>FAQ</span><span>CONTACT</span><span>GIFT CERTIFICATES</span>
</nav>

<section class="hero">
  <div class="abs ph-left" role="img" aria-label="Clinic technician with a happy client holding a first whitening sign"></div>
  <div class="abs hero-mid">
    <h1>Get That White Smile<br>You’ve Always Wanted</h1>
    <p>Amazing Results, The Most Effective System,<br>More Affordable Than The Dentist</p>
    <div class="reviews">
      <span class="review"><i></i>rateway</span>
      <span class="review"><i></i>searchly</span>
      <span class="review"><i></i>friendbook</span>
    </div>
    <div class="hero-social"><span>fk</span><span>ch</span><span>pb</span><span>PG</span></div>
  </div>
  <div class="abs ph-rt" role="img" aria-label="Group of smiling customers holding whitening studio signs"></div>
  <div class="abs ph-rb" role="img" aria-label="Selfie of three happy customers after whitening"></div>
</section>

<h2 class="abs about-h">BRIGHT HARBOR’S<b>SMILE STUDIO</b></h2>
<p class="abs about-sub">The best price, service and results.</p>
<p class="abs about-p">Bright Harbor Smile Studio features state-of-the-art technologies that are safe, industry-unique and very cost-effective. Our teeth whitening system utilizes the latest blue light whitening technology. Our Blue Light Systems are calibrated precisely for optimal activation of our exclusive hydrogen peroxide based whitening solution which is manufactured in a FDA registered facility in the USA.</p>
<div class="abs video" role="img" aria-label="Studio introduction video">
  <span class="play"><svg width="72" height="72" viewBox="0 0 72 72"><path d="M31 27l14 9-14 9z" fill="#fff"/></svg></span>
  <span class="vname">Bright Harbor</span>
</div>

<h2 class="sec-title" style="top:1098px">WHY <em>CHOOSE US</em></h2>
<div class="abs why">
  <div class="feature active"><div class="ring"><svg width="40" height="60" viewBox="0 0 40 60"><text x="6" y="48" font-family="Roboto" font-size="52" font-weight="700" fill="#fff">$</text></svg></div>Price</div>
  <div class="feature"><div class="ring"><svg width="46" height="40" viewBox="0 0 46 40" fill="none" stroke="#35b8d1" stroke-width="2"><path d="M2 38h42M6 38v-8h5v8M16 38v-13h5v13M26 38v-18h5v18M36 38v-24h5v24M4 24L20 12l8 6L42 3M36 3h6v6"/></svg></div>Results</div>
  <div class="feature"><div class="ring"><svg width="38" height="44" viewBox="0 0 38 44" fill="none" stroke="#35b8d1" stroke-width="2.4"><path d="M19 6C13 1 2 2 3 14c1 8 4 12 5 20 1 6 5 8 7 1l4-10 4 10c2 7 6 5 7-1 1-8 4-12 5-20 1-12-10-13-16-8z"/><path d="M10 10c2-2 5-2 7 0"/></svg></div>No Pain</div>
  <div class="feature"><div class="ring"><svg width="38" height="44" viewBox="0 0 38 44" fill="none" stroke="#35b8d1" stroke-width="2.2"><path d="M19 6C13 1 2 2 3 14c1 8 4 12 5 20 1 6 5 8 7 1l4-10 4 10c2 7 6 5 7-1 1-8 4-12 5-20 1-12-10-13-16-8z"/><circle cx="19" cy="17" r="5"/><circle cx="19" cy="17" r="9" stroke-dasharray="3 3"/></svg></div>Service</div>
  <div class="feature"><div class="ring"><svg width="44" height="44" viewBox="0 0 44 44" fill="none" stroke="#35b8d1" stroke-width="2"><path d="M4 40L33 11M31 7l6 6 4-4-6-6z"/></svg></div>Convenience</div>
  <div class="feature"><div class="ring"><svg width="42" height="42" viewBox="0 0 42 42" fill="none" stroke="#35b8d1" stroke-width="2.2"><path d="M3 18h8v21H3zM11 20l8-9 2-9c4 0 5 4 4 8l-1 6h12c3 0 4 3 3 5l-4 15c-1 2-2 3-4 3H11"/></svg></div>Guarantee</div>
</div>

<section class="abs how" role="img" aria-label="Clinic team photo with teal overlay">
  <h2>HOW IT WORKS</h2>
  <p>We have a very effective teeth whitening treatment that is guaranteed to get you quick results in about 1 hour. To start the treatment you’ll apply a Hydrogen Peroxide based whitening agent to your teeth. We then place our cold blue light directly in front of your exposed teeth for 15 minutes per treatment. The lighting systems we use activate the whitening agent and thats what accelerates the whitening process, giving you whiter teeth in less than an hour.</p>
  <span class="btn">READ MORE</span>
</section>

<h2 class="sec-title" style="top:1950px">COMPARE US</h2>
<table class="abs compare">
  <tr><th class="feat">Features</th><th style="width:200px">GLOWPRO</th><th class="hl" style="width:199px">BRIGHT HARBOR</th><th style="width:198px">LUMADENT</th><th>HOME KITS</th></tr>
  <tr><td class="feat">Speed</td><td>1-2 Hours</td><td class="hl">45 Mins</td><td>7-14 Days</td><td>7-30 Days</td></tr>
  <tr><td class="feat">Ease of Use</td><td>Difficult / Dentist</td><td class="hl">Very Easy</td><td>Difficult / Dentist</td><td>Difficult</td></tr>
  <tr><td class="feat">Cost</td><td>$300 - $600</td><td class="hl">$378</td><td>$300 - $600</td><td>$50 - $150</td></tr>
  <tr><td class="feat">Availability</td><td>Limited Availability</td><td class="hl">Appt Only</td><td>Limited Availability</td><td>Store Purchase</td></tr>
  <tr><td class="feat">Pain</td><td>Pain &amp; Sensitivity</td><td class="hl">No Pain</td><td>Sensitivity</td><td>Sensitivity</td></tr>
</table>

<h2 class="sec-title" style="top:2375px">TESTIMONIAL</h2>
<div class="abs quote"><span class="mark">66</span>Friendly staff. 3 step process-15 minute intervals. I am very pleased with results. Marisol was professional, polite and knowledgeable. I am apprehensive about any dental procedure but her patience and poise kept me calm through the duration of my treatment. I will be back again in the future</div>
<div class="abs avatar" role="img" aria-label="Customer portrait"></div>
<div class="abs t-meta">Lorem ipsum dolor sit amet, consectetur adipiscing elit<br>2 June<br><span class="link">Sed ut perspiciatis unde</span></div>
<span class="btn-outline more">See More Reviews</span>

<section class="abs f-band">
  <div class="f-item" style="left:112px"><span class="f-ico"><svg width="14" height="20" viewBox="0 0 24 34"><path fill="#fff" d="M12 0a12 12 0 00-12 12c0 9 12 22 12 22s12-13 12-22A12 12 0 0012 0zm0 17a5 5 0 110-10 5 5 0 010 10z"/></svg></span><span>location418 Harborview Way #205<br>Bayside, CA 90210</span></div>
  <div class="f-item" style="left:538px"><span class="f-ico"><svg width="22" height="22" viewBox="0 0 24 24" fill="none" stroke="#fff" stroke-width="2.4"><circle cx="12" cy="12" r="9"/><path d="M12 7v5h4"/></svg></span><span>Mon-Fri 9:15 am to 5:30 pm Sat 10am<br>to 2pm</span></div>
  <div class="f-item" style="left:930px"><span class="f-ico"><svg width="18" height="18" viewBox="0 0 24 24"><path fill="#fff" d="M6.6 10.8a15 15 0 006.6 6.6l2.2-2.2a1 1 0 011-.25 11.4 11.4 0 003.6.57 1 1 0 011 1V20a1 1 0 01-1 1A17 17 0 013 4a1 1 0 011-1h3.5a1 1 0 011 1c0 1.25.2 2.45.57 3.57a1 1 0 01-.25 1z"/></svg></span><span style="font-size:13px">1-555-014-2290</span></div>
</section>

<footer class="abs footer">
  <div class="fcol" style="left:114px"><h4>Quick Links</h4><ul><li>Home</li><li>Book Appointment Online</li><li>Our Process</li><li>Photos</li><li>Testimonials</li><li>Blog</li></ul></div>
  <div class="fcol" style="left:345px"><h4>Categories</h4><ul><li>Gift Certificates</li><li>After Care</li></ul></div>
  <div class="fcol" style="left:545px"><h4>Other Links</h4><ul><li>Consent Form Espanol</li><li>Consent Form English</li><li>&nbsp;Cancellation Policy</li><li>Privacy Policy</li><li>Free Treatments</li></ul></div>
  <div class="fcol" style="left:797px"><h4>Newsletter</h4><div class="news"><span>Email Address</span><b><svg width="22" height="20" viewBox="0 0 24 22"><path fill="#fff" d="M0 10L24 0l-4 22-7-6-4 5v-7l11-11-14 9z"/></svg></b></div></div>
</footer>

<div class="abs bottom">
  <span class="copy">© Copyrights.2018.Bright Harbor Smile Studio.All Rights Reserved</span>
  <span class="connect">Connect With Us : <b>fk</b><b>PG</b></span>
</div>

</body>
</html>
```